We are a recruitment company based in Norwich/Cambridge England.
I have included our company logo which we want to remain the same.

What we are looking for is a new creative Business card which will really stand out!!

Contact Information for Business Card

Harriet Dunmore
email: Harriet@plavex.co.uk
Address: Brackwell House
Fenmoor Enterprise Park
Partridge Way
Norwich
QB9 3KX
Tel:01632 960418

```html
<!DOCTYPE html>
<html lang="en">
<head>
<meta charset="utf-8">
<title>Plavex business card</title>
<link rel="stylesheet" href="https://fonts.googleapis.com/css2?family=Open+Sans:wght@400;600;700&display=swap">
<style>
  :root {
    --backdrop: #191919;
    --paper: #ffffff;
    --green: #8dc63f;
    --green-soft: #c6e39f;
    --grey: #8a8589;
    --grey-dark: #6e6a6d;
    --ink: #2b2b2b;
  }
  html, body {
    margin: 0;
    width: 1200px;
    height: 900px;
    overflow: hidden;
    background: var(--backdrop);
    font-family: "Open Sans", Arial, sans-serif;
  }
  .canvas { position: relative; width: 1200px; height: 900px; }
  .card {
    position: absolute;
    top: 306px;
    width: 440px;
    height: 271px;
    overflow: hidden;
  }
  .card-front { left: 149px; background: var(--paper); }
  .card-back { left: 608px; background: var(--green); }

  .brand {
    position: absolute;
    left: 196px;
    top: 50px;
    display: flex;
    align-items: center;
    gap: 12px;
  }
  .brand-dot {
    width: 40px; height: 40px;
    border-radius: 50%;
    background: var(--green);
  }
  .brand-name {
    font-size: 34px;
    font-weight: 600;
    color: var(--grey);
    letter-spacing: -0.5px;
  }

  .person { position: absolute; left: 24px; top: 146px; }
  .person-name {
    margin: 0;
    font-size: 16px;
    font-weight: 700;
    line-height: 18px;
    text-transform: uppercase;
    color: var(--grey-dark);
  }
  .person-name .first { color: var(--green); }
  .person-role { margin: 1px 0 0; font-size: 12px; color: var(--ink); }

  .divider {
    position: absolute;
    left: 24px; top: 190px;
    width: 368px; height: 1px;
    background: var(--green-soft);
  }
  .divider-dot {
    position: absolute;
    left: 396px; top: 183px;
    width: 15px; height: 15px;
    border-radius: 50%;
    border: 2px solid var(--green-soft);
    box-sizing: border-box;
  }

  .contact-list {
    position: absolute;
    list-style: none;
    margin: 0; padding: 0;
    font-size: 12.5px;
    line-height: 16px;
    color: var(--ink);
  }
  .contact-list li { display: flex; align-items: center; gap: 4px; }
  .contact-list svg { width: 9px; height: 9px; fill: var(--green); flex: none; }
  .contact-online { left: 23px; top: 220px; }
  .contact-phones { right: 22px; top: 205px; text-align: right; }
  .contact-phones li { justify-content: flex-end; }

  .back-panel {
    position: absolute;
    left: 0; top: 0;
    width: 220px; height: 271px;
    background: var(--grey);
  }
  .back-brand {
    position: absolute;
    inset: 0;
    display: flex;
    align-items: center;
    justify-content: center;
    gap: 16px;
  }
  .back-brand .brand-dot { width: 64px; height: 64px; background: var(--paper); }
  .back-brand .brand-name { font-size: 54px; color: var(--paper); }
</style>
</head>
<body>
<main class="canvas">
  <section class="card card-front" aria-label="Business card front">
    <div class="brand">
      <span class="brand-dot"></span>
      <span class="brand-name">Plavex</span>
    </div>

    <div class="person">
      <h1 class="person-name"><span class="first">Harriet</span> Dunmore</h1>
      <p class="person-role">Managing Director</p>
    </div>

    <div class="divider"></div>
    <div class="divider-dot"></div>

    <ul class="contact-list contact-online">
      <li>
        <svg viewBox="0 0 10 10"><path d="M0 2h10v6H0z M0 2l5 3.5L10 2" stroke="#fff" stroke-width="0.8"/></svg>
        Harriet@plavex.co.uk
      </li>
      <li>
        <svg viewBox="0 0 10 10"><circle cx="5" cy="5" r="5"/></svg>
        www.plavex.co.uk
      </li>
    </ul>

    <ul class="contact-list contact-phones">
      <li>01632 960418
        <svg viewBox="0 0 10 10"><path d="M0 4c0-2 2-3 5-3s5 1 5 3H7V3H3v1z M2 5h6l1 4H1z"/></svg>
      </li>
      <li>01632 960419
        <svg viewBox="0 0 10 10"><path d="M3 0h4a1 1 0 0 1 1 1v8a1 1 0 0 1-1 1H3a1 1 0 0 1-1-1V1a1 1 0 0 1 1-1zm0 1.5v6h4v-6z"/></svg>
      </li>
      <li>01632 960420
        <svg viewBox="0 0 10 10"><path d="M2 0h5v3H2z M0 3h10v5H8v2H2V8H0z M3 7v2h4V7z"/></svg>
      </li>
    </ul>
  </section>

  <section class="card card-back" aria-label="Business card back">
    <div class="back-panel"></div>
    <div class="back-brand">
      <span class="brand-dot"></span>
      <span class="brand-name">Plavex</span>
    </div>
  </section>
</main>
</body>
</html>
```